Graphic Design/Logo Needed for Ear Drops Bottle

We have an Ear Drop Medication that we need to create a new label for. We will use a retro picture of a Doctor (Dr. Bellamy) and the name of the product is Mighty Lobe. There is no official logo, so we will want to create a retro, basic logo for Mighty Lobe and use the retro picture. Front portion of the label is Size is 1.5" in height, and about 1.375" Width. this is a small tube similar in size to eye drops. We will be looking for just the logo portion and what you will see on the front of the bottle.

Target Market(s)

Medical Container

Industry/Entity Type

Medical

Font styles to use
Serif
Sans Serif

Colors
0054AA
0677BA
7BADD7
CADEEF
E8F1F8
FFF300
FFF600
FEFA6F
FFFEC7
FFFEE8

Requirements
Must have
• Picture of Dr. Bellamy, "Mighty Lobe", Dr. Bellamy's Ear Solution
Nice to have
• Retro Style or Modern with Retro Feel, Clean and engaging

```html
<!DOCTYPE html>
<html lang="en">
<head>
<meta charset="utf-8">
<title>Mighty Lobe – Ear Drops Label</title>
<link href="https://fonts.googleapis.com/css2?family=Playfair+Display:wght@700&family=Pathway+Gothic+One&display=swap" rel="stylesheet">
<style>
  :root {
    --navy: #0e3f73;
    --panel: #cadeef;
    --trim: #7badd7;
    --paper: #ffffff;
  }
  html, body {
    margin: 0;
    width: 1200px;
    height: 773px;
    overflow: hidden;
    background: var(--paper);
  }
  .stage {
    width: 1200px;
    height: 773px;
    display: flex;
    align-items: center;
    justify-content: center;
  }
  .label { display: block; }
  .label-sheet { fill: var(--paper); stroke: var(--trim); stroke-width: 2; }
  .label-panel { fill: var(--panel); stroke: var(--navy); stroke-width: 4; }
  .corner-dot, .pill, .size-badge { fill: var(--navy); }
  .rule { stroke: var(--navy); stroke-width: 4; fill: none; }
  .arch { fill: none; stroke: var(--navy); stroke-width: 4; }
  .arch-inner { fill: var(--paper); }
  .title-band { fill: var(--paper); }
  .product-name {
    font-family: "Playfair Display", serif;
    font-weight: 700;
    font-size: 150px;
    fill: var(--navy);
  }
  .tagline {
    font-family: "Pathway Gothic One", sans-serif;
    font-size: 42px;
    fill: var(--paper);
  }
  .net-weight {
    font-family: "Pathway Gothic One", sans-serif;
    font-size: 36px;
    fill: var(--navy);
  }
  .net-weight.badge-text { fill: var(--paper); font-size: 44px; }
</style>
</head>
<body>
<main class="stage">
  <svg class="label" width="642" height="699" viewBox="160 182 856 932" xmlns="http://www.w3.org/2000/svg">
    <defs>
      <linearGradient id="portraitTone" x1="0" y1="0" x2="0" y2="1">
        <stop offset="0" stop-color="#0e3f73"/>
        <stop offset="0.55" stop-color="#7badd7"/>
        <stop offset="1" stop-color="#e8f1f8"/>
      </linearGradient>
    </defs>

    <rect class="label-sheet" x="161" y="183" width="854" height="930"/>

    <path class="label-panel" d="M275,230 H893 A45,45 0 0 0 938,275 V1025 A45,45 0 0 0 893,1070 H275 A45,45 0 0 0 230,1025 V275 A45,45 0 0 0 275,230 Z"/>
    <circle class="corner-dot" cx="240" cy="242" r="10"/>
    <circle class="corner-dot" cx="925" cy="242" r="10"/>
    <circle class="corner-dot" cx="240" cy="1060" r="10"/>
    <circle class="corner-dot" cx="925" cy="1060" r="10"/>

    <g class="logo">
      <path class="arch" d="M432,598 A168,168 0 1 1 722,590"/>
      <line class="rule" x1="312" y1="600" x2="432" y2="600"/>
      <line class="rule" x1="722" y1="590" x2="843" y2="590"/>
      <circle class="arch-inner" cx="575" cy="515" r="143"/>
      <path role="img" aria-label="Retro illustration of Dr. Bellamy wearing a head mirror, shirt and tie"
            fill="url(#portraitTone)"
            d="M520,395 Q575,370 635,420 L645,520 Q640,570 620,590 L750,630 L420,630 L535,585 Q515,560 510,500 Z"/>
      <rect class="title-band" x="312" y="612" width="531" height="175"/>
      <text class="product-name" x="578" y="755" text-anchor="middle" textLength="480" lengthAdjust="spacingAndGlyphs">Mighty Lobe</text>
      <line class="rule" x1="310" y1="806" x2="845" y2="806"/>
      <rect class="pill" x="426" y="772" width="294" height="68" rx="34"/>
      <text class="tagline" x="577" y="820" text-anchor="middle" textLength="250" lengthAdjust="spacingAndGlyphs">Dr Bellamy's Ear Solution</text>
    </g>

    <g class="size">
      <text class="net-weight" x="545" y="1027" text-anchor="end">Nt. Wt.</text>
      <circle class="size-badge" cx="592" cy="1010" r="37"/>
      <text class="net-weight badge-text" x="592" y="1025" text-anchor="middle">2 oz</text>
      <text class="net-weight" x="638" y="1027">59 ml</text>
    </g>
  </svg>
</main>
</body>
</html>
```